Velour Detailing – Premium Automotive Detailing Studio Website Design

We're launching a premium automotive detailing studio called Velour Detailing, and we’re looking for a clean, minimal, and high-end website design (desktop + mobile version). The studio targets owners of luxury vehicles who care deeply about aesthetics, perfection, and exceptional service.
This project is about more than just showing services , it should feel like a luxury experience from the very first second. The design should be modern, minimalistic, elegant, and clearly aimed at an upscale market.
We’re looking for a designer who can translate our physical studio’s premium interior and architectural feel into a digital presence.
What we want the website to feel like:
Clean and modern
Professional and luxurious
Minimal and not cluttered
Light animations or transitions to add polish
Stylish and cinematic
Design freedom:
We trust your design direction. We are not providing strict color codes or layout instructions, we want you to create what you believe works best based on our brand positioning and target audience. Just keep it premium, modern, and well-organized.
What the website should include:
Hero section with a bold visual (image or video)
About the Studio — a few blocks explaining our story and focus on quality
Service Overview — clearly showing what we offer (detailing, ceramic coating, interior, etc.)
Gallery/Showcase — show off our work with cars, interior, and the space itself
Client Lounge Area — mention comfort, coffee, and waiting space
Testimonials — social proof from satisfied clients
Location & contact section — map, address, contact form
Footer, simple with nav, contact info, and optional social media
Target audience:
Owners of high-end vehicles (Valtrane, Korvel, etc.)
Car collectors and detailing enthusiasts
People looking for premium-level service and presentation
Brands/creators booking our photo studio

```html
<!DOCTYPE html>
<html lang="en">
<head>
<meta charset="utf-8">
<title>Velour Detailing – Client Lounge &amp; Testimonials</title>
<link href="https://fonts.googleapis.com/css2?family=Noto+Sans:wght@400;500&display=swap" rel="stylesheet">
<style>
  :root {
    --ink: #0d0d0d;
    --paper: #ffffff;
    --dark-1: #050505;
    --dark-2: #3a3a3a;
    --light-1: #f7f7f7;
    --light-2: #e4e4e4;
    --gold: #f5a800;
    --rule: #d9d9d9;
  }
  * { margin: 0; padding: 0; box-sizing: border-box; }
  html, body { width: 1200px; height: 1200px; overflow: hidden; }
  body { font-family: "Noto Sans", sans-serif; color: var(--ink); background: var(--paper); position: relative; }

  .lounge { position: absolute; left: 0; top: 0; width: 1200px; height: 485px; overflow: hidden;
    background: linear-gradient(135deg, var(--dark-1) 0%, #2a2a2a 35%, #4a4a4a 55%, #161616 80%, var(--dark-1) 100%); }
  .lounge-photo { position: absolute; inset: 0;
    background: linear-gradient(120deg, #a89c8c 0%, #6d5f52 40%, #2f2a26 70%, #8b8378 100%);
    clip-path: polygon(801px 0, 1200px 0, 1200px 485px, 565px 485px); }
  .lounge-title { position: absolute; left: 92px; top: 116px; color: var(--paper);
    font-size: 57px; font-weight: 400; line-height: 56px; letter-spacing: 0.5px; }
  .lounge-text { position: absolute; left: 92px; top: 260px; width: 500px; color: #e8e8e8;
    font-size: 13.4px; line-height: 20px; }
  .lounge-mark { position: absolute; left: 91px; top: 337px; }
  .lounge-rule { position: absolute; left: 104px; top: 355px; width: 774px; height: 1px; background: var(--rule); }

  .testimonials { position: absolute; left: 0; top: 485px; width: 1200px; height: 643px;
    background: linear-gradient(160deg, var(--light-1) 0%, #ececec 30%, #fafafa 55%, var(--light-2) 80%, #f4f4f4 100%); }
  .section-title { text-align: center; font-size: 53px; font-weight: 400; letter-spacing: 1px; }
  .testimonials .section-title { margin-top: 33px; line-height: 64px; }
  .review { position: absolute; top: 164px; width: 290px; text-align: center; }
  .review-photo { width: 255px; height: 273px; border-radius: 50%; margin: 0 auto;
    background: radial-gradient(circle at 50% 40%, #c9a189 0%, #8a7464 45%, #3c3f4a 100%); }
  .review-text { margin-top: 52px; font-size: 13px; line-height: 20px; color: #1a1a1a; }
  .review-rating { display: flex; justify-content: center; gap: 6px; margin-top: 18px; }

  .contact { position: absolute; left: 0; top: 1128px; width: 1200px; height: 72px; background: var(--paper); }
  .contact .section-title { margin-top: 33px; line-height: 64px; }
</style>
</head>
<body>
  <section class="lounge">
    <div class="lounge-photo" role="img" aria-label="Guests relaxing with drinks on leather sofas in the studio client lounge"></div>
    <h1 class="lounge-title">CLIENT LOUNGE<br>AREA</h1>
    <p class="lounge-text">lorem ipsum dolor sit amet, consectetur et dolore gna aliqua. enim ad minim veniam, adipiscing elit,&nbsp; eiusmod tempor incididunt ut labore eu fugiat nulla et dolore gna aliqua. enim ad minim veniam, eu fugiat nulla pariatur.</p>
    <svg class="lounge-mark" width="26" height="20" viewBox="0 0 26 20"><path d="M6 1h14l5 6-12 12L1 7z" fill="#fff"/><path d="M1 7h24" stroke="#bbb" stroke-width="1"/></svg>
    <div class="lounge-rule"></div>
  </section>

  <section class="testimonials">
    <h2 class="section-title">TESTIMONIALS</h2>

    <article class="review" style="left:101px">
      <div class="review-photo" role="img" aria-label="Portrait of a satisfied client"></div>
      <p class="review-text">lorem ipsum dolor sit amet, consectetur adipiscing elit,&nbsp; eiusmod tempor incididunt et dolore gna aliqua. enim ad minim</p>
      <div class="review-rating" aria-label="5 of 5">
        <svg width="24" height="18" viewBox="0 0 24 18"><path d="M5 0h14l5 6-12 12L0 6z" fill="var(--gold)"/></svg>
        <svg width="24" height="18" viewBox="0 0 24 18"><path d="M5 0h14l5 6-12 12L0 6z" fill="var(--gold)"/></svg>
        <svg width="24" height="18" viewBox="0 0 24 18"><path d="M5 0h14l5 6-12 12L0 6z" fill="var(--gold)"/></svg>
        <svg width="24" height="18" viewBox="0 0 24 18"><path d="M5 0h14l5 6-12 12L0 6z" fill="var(--gold)"/></svg>
        <svg width="24" height="18" viewBox="0 0 24 18"><path d="M5 0h14l5 6-12 12L0 6z" fill="var(--gold)"/></svg>
      </div>
    </article>

    <article class="review" style="left:457px">
      <div class="review-photo" role="img" aria-label="Portrait of a satisfied client"></div>
      <p class="review-text">lorem ipsum dolor sit amet, consectetur adipiscing elit,&nbsp; eiusmod tempor incididunt et dolore gna aliqua. enim ad minim</p>
      <div class="review-rating" aria-label="5 of 5">
        <svg width="24" height="18" viewBox="0 0 24 18"><path d="M5 0h14l5 6-12 12L0 6z" fill="var(--gold)"/></svg>
        <svg width="24" height="18" viewBox="0 0 24 18"><path d="M5 0h14l5 6-12 12L0 6z" fill="var(--gold)"/></svg>
        <svg width="24" height="18" viewBox="0 0 24 18"><path d="M5 0h14l5 6-12 12L0 6z" fill="var(--gold)"/></svg>
        <svg width="24" height="18" viewBox="0 0 24 18"><path d="M5 0h14l5 6-12 12L0 6z" fill="var(--gold)"/></svg>
        <svg width="24" height="18" viewBox="0 0 24 18"><path d="M5 0h14l5 6-12 12L0 6z" fill="var(--gold)"/></svg>
      </div>
    </article>

    <article class="review" style="left:813px">
      <div class="review-photo" role="img" aria-label="Portrait of a satisfied client"></div>
      <p class="review-text">lorem ipsum dolor sit amet, consectetur adipiscing elit,&nbsp; eiusmod tempor incididunt et dolore gna aliqua. enim ad minim</p>
      <div class="review-rating" aria-label="5 of 5">
        <svg width="24" height="18" viewBox="0 0 24 18"><path d="M5 0h14l5 6-12 12L0 6z" fill="var(--gold)"/></svg>
        <svg width="24" height="18" viewBox="0 0 24 18"><path d="M5 0h14l5 6-12 12L0 6z" fill="var(--gold)"/></svg>
        <svg width="24" height="18" viewBox="0 0 24 18"><path d="M5 0h14l5 6-12 12L0 6z" fill="var(--gold)"/></svg>
        <svg width="24" height="18" viewBox="0 0 24 18"><path d="M5 0h14l5 6-12 12L0 6z" fill="var(--gold)"/></svg>
        <svg width="24" height="18" viewBox="0 0 24 18"><path d="M5 0h14l5 6-12 12L0 6z" fill="var(--gold)"/></svg>
      </div>
    </article>
  </section>

  <section class="contact">
    <h2 class="section-title">LOCATION &amp; CONTACT SECTION</h2>
  </section>
</body>
</html>
```